Millcrest PTA Website Design

We are working with Millcrest Elementary School PTA. They are a Parent Teacher Association that needs a new website design.

A Parent Teacher Association (PTA) is a volunteer organization that brings parents, teachers, and school staff together to support students and enhance their educational experience. PTAs organize fundraisers, sponsor school events, advocate for education policies, and foster stronger connections between families and schools.

Some sites to use for inspiration:

https://parentboardhub.com/demo/
https://nonprofits.kindlyfundr.com/blogs/more-great-pta-websites-you-should-copy
https://www.rvmxpta.com

Thank you for taking the time to consider designing a website for us. We are web developers based in Stockton and Los Angeles, CA, USA. Most of our projects go through the same process. Understanding this process may help you win a project with us. We custom-code all of our websites in-house. We don’t have any requirements as to what tools you use for your design, but we prefer Figma files. For any design that we label as four-stars, we send it to the client for review. The client picks the final design they want us to use. Once we complete this process, we will continue to show additional clients all the four-star sites and purchase them later. Your designs will have multiple chances to sell. For better chances of success, we ask that you follow these guidelines.

IMAGES:
If you use any images or icons in the design, we ask that you have a link to the asset so we can purchase the image/icon. Most of the designs we submit do not have the customer’s images on them unless they have some great images. Be creative; show us the feeling you are trying to portray with your image choices. Use any royalty-free site you choose. We subscribe to Adobe and mainly use their images, but we can purchase images outside of Adobe.

PLEASE NOTE: we will not submit designs to clients with watermarks on the images.

FONTS:
We ask that you identify the fonts used in the design. This can be done in a message if you want. We typically use Google Fonts and Adobe Fonts.

CONTENT:
We're always open to different content and ideas. We often submit designs with stock images so the client can see our vision. We typically take pictures after the website launch to use their images with our vision. Lorem Ipsum is fine for paragraphs, but we ask that you write the headers in correct English. We want to be able to show the vision and identify the sections of the website.

INSPIRATION:
We typically add a couple of links in the brief of websites we like to help you get started in your design.

REVISIONS:
We do not often ask for revisions of the designs unless we see something in the design that may not appeal to the client. If there are slight changes that we want to make, we do that in the development process.

FEEDBACK:
We rarely give feedback on designs during the design process. We are working on many website projects and do not have the time to provide feedback. We usually respond if your request is well thought out and asks specific questions, but a note asking “feedback, please” usually goes unanswered.

```html
<!DOCTYPE html>
<html lang="en">
<head>
<meta charset="utf-8">
<title>Millcrest PTA</title>
<link href="https://fonts.googleapis.com/css2?family=Oswald:wght@400;500;600&family=Open+Sans:wght@400;600;700&display=swap" rel="stylesheet">
<style>
:root{
  --navy:#1f3f8d;
  --navy-deep:#183477;
  --white:#ffffff;
  --ink:#1d1d1d;
  --text:#3a3a3a;
  --muted:#6b6b6b;
  --line:#d9d9d9;
  --teal:#3aaa8c;
}
*{box-sizing:border-box;margin:0;padding:0}
html,body{width:1200px;height:3862px;overflow:hidden;background:var(--white)}
body{font-family:"Open Sans",sans-serif;color:var(--text);position:relative}
.abs{position:absolute}
.heading{font-family:"Oswald",sans-serif;font-weight:500;color:var(--navy);line-height:1.2}

/* header */
.topbar{left:0;top:0;width:1200px;height:68px;background:var(--white)}
.brand{left:112px;top:14px;font-family:"Oswald",sans-serif;font-weight:600;font-size:30px;line-height:40px;color:var(--navy);letter-spacing:1px}
.contact-chip{top:16px;display:flex;align-items:center;gap:12px;font-family:"Oswald",sans-serif;font-size:17px;line-height:36px;color:var(--ink)}
.contact-chip b{color:var(--navy);font-weight:500}
.ring{width:36px;height:36px;border:2px solid var(--navy);border-radius:50%;display:flex;align-items:center;justify-content:center}
.socials{left:973px;top:16px;display:flex;gap:4px}
.socials span{width:36px;height:36px;border:2px solid var(--navy);border-radius:50%;display:block}
.navbar{left:0;top:68px;width:1200px;height:46px;background:var(--navy)}
.nav{position:absolute;top:0;left:0;width:1200px;height:46px;font-family:"Oswald",sans-serif;font-size:16px;line-height:22px;color:var(--white);text-transform:uppercase}
.nav span{position:absolute;top:12px;transform:translateX(-50%);white-space:nowrap}
.nav .active{font-weight:600}

/* hero */
.hero{left:0;top:114px;width:1200px;height:560px;overflow:hidden}
.hero-photo{position:absolute;inset:0;background:linear-gradient(90deg,#8d8579 0%,#b9b0a2 30%,#d8d0c2 45%,#c9b79e 60%,#a89a88 80%,#cfc7bb 100%)}
.hero-title{left:110px;top:100px;font-family:"Oswald",sans-serif;font-weight:500;font-size:60px;line-height:64px;color:var(--white);letter-spacing:1px}
.hero-copy{left:111px;top:172px;width:370px;font-size:15px;line-height:26px;color:var(--white)}
.btn-outline{left:110px;top:272px;width:126px;height:46px;border:2px solid var(--white);background:var(--navy);color:var(--white);font-family:"Oswald",sans-serif;font-size:15px;display:flex;align-items:center;justify-content:center}

/* pta and you */
.section-title{width:1200px;left:0;text-align:center}
.card{width:470px;height:447px;border:2px solid var(--navy);background:var(--white)}
.card-photo{position:absolute;left:15px;top:14px;width:437px;height:222px}
.card h3{position:absolute;top:258px;width:100%;text-align:center;font-family:"Oswald",sans-serif;font-weight:500;font-size:24px;line-height:32px;color:var(--ink)}
.card p{position:absolute;top:302px;left:16px;width:436px;text-align:center;font-size:14.5px;line-height:24px;color:var(--text)}
.arrow{width:30px;height:30px;border:1.5px solid var(--ink);border-radius:50%;display:flex;align-items:center;justify-content:center}

/* partner strip */
.strip{left:0;top:1406px;width:1200px;height:160px;background:var(--white);box-shadow:0 -4px 10px rgba(0,0,0,.06)}
.strip-divider{top:36px;width:1.5px;height:92px;background:#9a9a9a}

/* services */
.services{left:0;top:1566px;width:1200px;height:655px;background:var(--navy);overflow:hidden}
.services-title{top:70px;font-family:"Open Sans",sans-serif;font-weight:600;font-size:36px;line-height:46px;color:var(--white)}
.underline{height:3px;background:var(--white)}
.svc-photo{width:286px;height:228px;border-radius:18px}
.svc-box{width:264px;height:102px;background:var(--white);border-radius:12px;padding:14px 16px}
.svc-box h4{font-weight:700;font-size:18px;line-height:24px;color:var(--ink);display:flex;justify-content:space-between;align-items:center}
.svc-box h4 i{width:21px;height:21px;border:1.5px solid var(--navy);border-radius:50%;display:flex;align-items:center;justify-content:center}
.svc-box p{margin-top:6px;font-size:13px;line-height:20px;color:var(--text)}

/* store */
.store-title{left:110px;top:2308px;font-size:36px}
.store-copy{left:111px;top:2392px;width:460px;font-size:15.5px;line-height:27.5px;color:var(--text)}
.store-copy p{margin-bottom:27px}
.store-copy a{color:var(--navy);font-weight:600;text-decoration:none}
.btn-solid{left:111px;top:2685px;width:133px;height:46px;background:var(--navy);color:var(--white);font-weight:600;font-size:15px;display:flex;align-items:center;justify-content:center}

/* contact */
.contact{left:0;top:2829px;width:1200px;height:577px;background:var(--navy)}
.contact-title{top:82px;font-family:"Oswald",sans-serif;font-weight:500;font-size:38px;line-height:48px;color:var(--white)}
.info-icon{width:80px;height:80px;border:2px solid var(--white);border-radius:50%;display:flex;align-items:center;justify-content:center}
.info-label{font-family:"Oswald",sans-serif;font-weight:500;font-size:15px;color:var(--white)}
.info-value{font-size:14px;line-height:26px;color:var(--white)}
.field{border:2px solid var(--white);border-radius:3px;color:var(--white);font-size:14px;padding:12px 16px}
.submit{left:481px;top:432px;width:134px;height:46px;background:var(--white);color:var(--navy);font-family:"Oswald",sans-serif;font-weight:500;font-size:19px;display:flex;align-items:center;justify-content:center}

/* footer */
.footer-brand{left:115px;top:3570px;font-family:"Oswald",sans-serif;font-weight:600;font-size:38px;line-height:48px;color:var(--navy);letter-spacing:1px}
.footer-brand-mark{left:115px;top:3502px;width:56px;height:56px;background:var(--navy)}
.col-title{font-weight:600;font-size:20px;line-height:28px;color:var(--ink);letter-spacing:.5px}
.col-rule{height:2px;background:var(--line)}
.foot-item{display:flex;gap:14px;font-size:15px;line-height:27px;color:var(--text)}
.foot-dot{flex:none;width:24px;height:24px;border-radius:50%;background:var(--navy);margin-top:6px;display:flex;align-items:center;justify-content:center}
.menu-list{font-size:15px;line-height:31px;color:var(--text);list-style:none}
.copyright{left:0;top:3805px;width:1200px;text-align:center;font-size:14.5px;color:var(--text)}
.footer-rule{left:60px;top:3775px;width:1080px;height:1px;background:var(--line)}
</style>
</head>
<body>

<header>
  <div class="abs topbar">
    <div class="abs brand">MILLCREST</div>
    <div class="abs contact-chip" style="left:437px">
      <span class="ring"><svg width="16" height="16" viewBox="0 0 24 24"><path d="M6.6 10.8a15.1 15.1 0 0 0 6.6 6.6l2.2-2.2a1 1 0 0 1 1-.25 11.4 11.4 0 0 0 3.6.57 1 1 0 0 1 1 1V20a1 1 0 0 1-1 1A17 17 0 0 1 3 4a1 1 0 0 1 1-1h3.5a1 1 0 0 1 1 1c0 1.25.2 2.45.57 3.57a1 1 0 0 1-.25 1z" fill="#1f3f8d"/></svg></span>
      <span><b>Phone:</b> (209)555-0147</span>
    </div>
    <div class="abs contact-chip" style="left:669px">
      <span class="ring"><svg width="16" height="14" viewBox="0 0 24 20"><rect x="1" y="1" width="22" height="18" rx="2" fill="#1f3f8d"/><path d="M2 3l10 8 10-8" stroke="#fff" stroke-width="2" fill="none"/></svg></span>
      <span><b>Mail:</b> hello@millcrestpta.org</span>
    </div>
    <div class="abs socials" aria-label="Social links"><span></span><span></span><span></span></div>
  </div>
  <nav class="abs navbar">
    <div class="nav">
      <span class="active" style="left:332px">Home</span>
      <span style="left:435px">PTA and You!</span>
      <span style="left:585px">Millcrest PTA Store</span>
      <span style="left:762px">PTA-Funded Progams</span>
      <span style="left:922px">Blue and White</span>
      <span style="left:1052px">Contact Us</span>
    </div>
  </nav>
</header>

<section class="abs hero">
  <div class="hero-photo" role="img" aria-label="Photo of two students talking with a teacher holding a tablet in a school hallway"></div>
  <h1 class="abs hero-title">MILLCREST PTA</h1>
  <p class="abs hero-copy">Also, you can't leave home without your Millcrest Spirit Wear! Choose your style and size below then check out using your credit</p>
  <div class="abs btn-outline">GET STARTED</div>
</section>

<section>
  <h2 class="abs section-title heading" style="top:778px;font-size:42px">PTA and You!</h2>
  <div class="abs arrow" style="left:39px;top:1069px"><svg width="10" height="12" viewBox="0 0 10 12"><path d="M7 1L2 6l5 5" stroke="#1d1d1d" stroke-width="1.6" fill="none"/></svg></div>
  <div class="abs arrow" style="left:1131px;top:1069px"><svg width="10" height="12" viewBox="0 0 10 12"><path d="M3 1l5 5-5 5" stroke="#1d1d1d" stroke-width="1.6" fill="none"/></svg></div>

  <article class="abs card" style="left:110px;top:860px">
    <div class="card-photo" role="img" aria-label="Photo of smiling students chatting around a laptop" style="background:linear-gradient(120deg,#6f5a44,#a88a66 45%,#4f7fae 75%,#c9b8a0)"></div>
    <h3>Millcrest Yearbook</h3>
    <p>Parents, students, family and friends!&nbsp; Break out that camera and snap those pics!&nbsp; 1st day of school, Red Ribbon Week, Spirit days - whatever the event, we want your photos!</p>
    <div class="abs" role="img" aria-label="Colourful yearbook lettering badge" style="left:165px;top:395px;width:136px;height:38px;border-radius:8px;background:linear-gradient(90deg,#e0407a,#f3a43a,#7b4fc4)"></div>
  </article>

  <article class="abs card" style="left:618px;top:860px">
    <div class="card-photo" role="img" aria-label="Photo of a teacher helping students in a classroom library" style="background:linear-gradient(120deg,#bdb8ae,#8a7a66 40%,#c79a4b 70%,#e3ded5)"></div>
    <h3>Important DAtes</h3>
    <p>Parents, students, family and friends!&nbsp; Break out that camera and snap those pics!&nbsp; 1st day of school, Red Ribbon Week, Spirit days - whatever the event, we want your photos!</p>
    <div class="abs" style="left:206px;top:382px;width:56px;height:56px;border-radius:50%;background:var(--teal);display:flex;align-items:center;justify-content:center">
      <svg width="30" height="30" viewBox="0 0 30 30"><rect x="3" y="5" width="24" height="22" rx="2" fill="#fff"/><rect x="3" y="5" width="24" height="6" fill="#dfeee9"/><g fill="#9bbfb4"><rect x="7" y="14" width="4" height="3"/><rect x="13" y="14" width="4" height="3"/><rect x="19" y="14" width="4" height="3"/><rect x="7" y="20" width="4" height="3"/><rect x="13" y="20" width="4" height="3"/><rect x="19" y="20" width="4" height="3"/></g></svg>
    </div>
  </article>
</section>

<section class="abs strip">
  <div class="abs" style="left:222px;top:60px;font-family:'Oswald',sans-serif;font-weight:600;font-size:26px;line-height:36px;color:var(--navy)">MILLCREST</div>
  <div class="abs strip-divider" style="left:345px"></div>
  <div class="abs" style="left:392px;top:64px;font-family:'Oswald',sans-serif;font-weight:600;font-size:21px;line-height:30px;color:var(--navy)">MILLCREST LIONS</div>
  <div class="abs strip-divider" style="left:596px"></div>
  <div class="abs" role="img" aria-label="Fall carnival event flyer" style="left:680px;top:20px;width:94px;height:120px;background:linear-gradient(180deg,#e9a04a,#f2c97a 50%,#e07a3a)"></div>
  <div class="abs strip-divider" style="left:847px"></div>
  <div class="abs" role="img" aria-label="Volunteer graphic with colourful raised hands" style="left:914px;top:48px;width:140px;height:76px;background:linear-gradient(90deg,#e85b5b,#f5c244,#5bbf6a,#4c8fe0,#a45bd8)"></div>
</section>

<section class="abs services">
  <h2 class="abs section-title services-title">Our Services</h2>
  <div class="abs underline" style="left:570px;top:122px;width:60px"></div>

  <div class="abs svc-photo" role="img" aria-label="Photo of children painting together" style="left:112px;top:169px;background:linear-gradient(135deg,#d9c4a5,#c86b7d 40%,#4f8fc0 70%,#e3d3b8)"></div>
  <div class="abs svc-box" style="left:123px;top:397px"><h4>Art Program <i><svg width="8" height="10" viewBox="0 0 8 10"><path d="M2 1l4 4-4 4" stroke="#1f3f8d" stroke-width="1.5" fill="none"/></svg></i></h4><p>Through fundraising and generous donations, our PTA fully funds</p></div>

  <div class="abs svc-photo" role="img" aria-label="Photo of a teacher with students raising hands in class" style="left:435px;top:212px;background:linear-gradient(135deg,#d8cfbe,#b59677 45%,#6d88a8 75%,#e2d9c8)"></div>
  <div class="abs svc-box" style="left:446px;top:440px"><h4>Teacher Supplies <i><svg width="8" height="10" viewBox="0 0 8 10"><path d="M2 1l4 4-4 4" stroke="#1f3f8d" stroke-width="1.5" fill="none"/></svg></i></h4><p>With education budgets being tightened</p></div>

  <div class="abs svc-photo" role="img" aria-label="Photo of students on a field trip in a park" style="left:759px;top:169px;background:linear-gradient(135deg,#7fa05a,#4f6f3a 45%,#a5b48a 75%,#6c8a4e)"></div>
  <div class="abs svc-box" style="left:770px;top:397px"><h4>Field Trips <i><svg width="8" height="10" viewBox="0 0 8 10"><path d="M2 1l4 4-4 4" stroke="#1f3f8d" stroke-width="1.5" fill="none"/></svg></i></h4><p>Out-of-class experiences are often the ones</p></div>

  <div class="abs svc-photo" role="img" aria-label="Photo of children building a robotics project" style="left:1087px;top:203px;background:linear-gradient(135deg,#cfc8bd,#8b7f70 50%,#b9aea0)"></div>
  <div class="abs svc-box" style="left:1099px;top:431px"><h4>STEM</h4><p>We love STEM and seeing kids exploring</p></div>
</section>

<section>
  <h2 class="abs heading store-title">Millcrest PTA Store</h2>
  <div class="abs" style="left:111px;top:2361px;width:68px;height:3px;background:var(--navy)"></div>
  <div class="abs store-copy">
    <p>Don't be caught unprepared! Join PTA and make a difference.</p>
    <p>Yearbooks are where it's at!&nbsp; Snap those photos of school events and fun days at Millcrest then send them over to <a>yearbook@millcrestpta.org!</a></p>
    <p>Also, you can't leave home without your Millcrest Spirit Wear! Choose your style and size below then check out using your credit/debit card or PayWallet. We can't wait to see you show off your Lion Pride...even if it's only virtually right now!</p>
  </div>
  <div class="abs btn-solid">Learn More</div>
  <div class="abs" style="left:649px;top:2317px;width:416px;height:416px;border-radius:50%;border:2px solid var(--navy)"></div>
  <div class="abs" role="img" aria-label="Photo of a parent and teacher reviewing papers together" style="left:668px;top:2336px;width:378px;height:378px;border-radius:50%;background:linear-gradient(135deg,#c9c2b6,#8a6a55 40%,#3f4f6e 70%,#d2cbc0)"></div>
</section>

<section class="abs contact">
  <h2 class="abs section-title contact-title">Contact Us</h2>
  <div class="abs" style="left:577px;top:139px;width:46px;height:3px;background:var(--white)"></div>

  <div class="abs info-icon" style="left:135px;top:173px"><svg width="36" height="28" viewBox="0 0 36 28"><rect x="1" y="1" width="34" height="26" rx="2" fill="#fff"/><path d="M2 3l16 12 16-12" stroke="#1f3f8d" stroke-width="2.5" fill="none"/></svg></div>
  <div class="abs info-label" style="left:243px;top:190px">EMAIL:</div>
  <div class="abs info-value" style="left:243px;top:216px">hello@millcrestpta.org</div>

  <div class="abs info-icon" style="left:135px;top:278px"><svg width="34" height="34" viewBox="0 0 24 24"><path d="M6.6 10.8a15.1 15.1 0 0 0 6.6 6.6l2.2-2.2a1 1 0 0 1 1-.25 11.4 11.4 0 0 0 3.6.57 1 1 0 0 1 1 1V20a1 1 0 0 1-1 1A17 17 0 0 1 3 4a1 1 0 0 1 1-1h3.5a1 1 0 0 1 1 1c0 1.25.2 2.45.57 3.57a1 1 0 0 1-.25 1z" fill="none" stroke="#fff" stroke-width="1.6"/></svg></div>
  <div class="abs info-label" style="left:243px;top:295px">PHONE:</div>
  <div class="abs info-value" style="left:243px;top:321px">(209)555-0147</div>

  <div class="abs info-icon" style="left:135px;top:380px"><svg width="30" height="36" viewBox="0 0 30 36"><path d="M15 2a11 11 0 0 1 11 11c0 8-11 19-11 19S4 21 4 13A11 11 0 0 1 15 2z" fill="none" stroke="#fff" stroke-width="2.2"/><circle cx="15" cy="13" r="4" fill="none" stroke="#fff" stroke-width="2.2"/><path d="M6 34h18" stroke="#fff" stroke-width="2.2"/></svg></div>
  <div class="abs info-label" style="left:243px;top:386px">ADDRESS:</div>
  <div class="abs info-value" style="left:243px;top:412px">1418 Orchard Bend Lane<br>Riverton, CA 95390</div>

  <div class="abs field" style="left:481px;top:173px;width:285px;height:52px">First Name</div>
  <div class="abs field" style="left:775px;top:173px;width:285px;height:52px">Last Name</div>
  <div class="abs field" style="left:481px;top:235px;width:285px;height:52px">Phone Number</div>
  <div class="abs field" style="left:775px;top:235px;width:285px;height:52px">Email</div>
  <div class="abs field" style="left:481px;top:300px;width:579px;height:112px">Message</div>
  <div class="abs submit">Submit</div>
</section>

<footer>
  <div class="abs footer-brand-mark"></div>
  <div class="abs footer-brand">MILLCREST</div>

  <div class="abs col-title" style="left:351px;top:3490px">CONTACT US</div>
  <div class="abs col-rule" style="left:351px;top:3526px;width:207px"></div>
  <div class="abs" style="left:351px;top:3548px;width:300px">
    <div class="foot-item"><span class="foot-dot"><svg width="10" height="12" viewBox="0 0 10 12"><path d="M5 0a4 4 0 0 1 4 4c0 3-4 8-4 8S1 7 1 4a4 4 0 0 1 4-4z" fill="#fff"/></svg></span><span>1418 Orchard Bend Lane<br>Riverton, CA 95390</span></div>
    <div class="foot-item" style="margin-top:10px"><span class="foot-dot"><svg width="12" height="12" viewBox="0 0 24 24"><path d="M6.6 10.8a15.1 15.1 0 0 0 6.6 6.6l2.2-2.2a1 1 0 0 1 1-.25 11.4 11.4 0 0 0 3.6.57 1 1 0 0 1 1 1V20a1 1 0 0 1-1 1A17 17 0 0 1 3 4a1 1 0 0 1 1-1h3.5a1 1 0 0 1 1 1c0 1.25.2 2.45.57 3.57a1 1 0 0 1-.25 1z" fill="#fff"/></svg></span><span>Call Us<br>(209)555-0147</span></div>
    <div class="foot-item" style="margin-top:10px"><span class="foot-dot"><svg width="12" height="9" viewBox="0 0 12 9"><rect width="12" height="9" rx="1" fill="#fff"/><path d="M1 1l5 4 5-4" stroke="#1f3f8d" fill="none"/></svg></span><span>E mail Us<br>hello@millcrestpta.org</span></div>
  </div>

  <div class="abs col-title" style="left:733px;top:3490px">MENU</div>
  <div class="abs col-rule" style="left:733px;top:3526px;width:116px"></div>
  <ul class="abs menu-list" style="left:736px;top:3538px">
    <li>HOME</li><li>ABOUT</li><li>COACHING</li><li>SPEAKING</li><li>FAQ</li>
  </ul>

  <div class="abs col-title" style="left:967px;top:3490px">FOLLOW US</div>
  <div class="abs" style="left:967px;top:3548px;width:180px">
    <div class="foot-item"><span class="foot-dot"></span><span>Like us on<br>FRIENDSBOOK</span></div>
    <div class="foot-item" style="margin-top:10px"><span class="foot-dot"></span><span>Follow us on<br>Snapgram</span></div>
    <div class="foot-item" style="margin-top:10px"><span class="foot-dot"></span><span>Follow us on<br>WORKMESH</span></div>
  </div>

  <div class="abs footer-rule"></div>
  <div class="abs copyright">Copyright © 2023 All Rights Reserved</div>
</footer>

</body>
</html>
```